Telecommunications/Power civil contractor needs business card design

Were a new telecommunications/power underground civil contractor that is looking for a new business card design. Our company colours are silver or grey and orange. Feel free to use the white background logo or the black background logo.

Target Market(s)

Local contractors, utility companies, private sector mining/energy companies, developers.

Industry/Entity Type

Telecommunications

Contact Information for Business Card

Each card will need the following info:
Persons name:
Title:
E-mail:
Phone number:
Shop Address:
Mailing Address:

Requirements
Must have
• Each card will need the following info:
• Persons name:
• Title:
• E-mail:
• Phone number:
• Shop Address:
• Mailing Address:

```html
<!DOCTYPE html>
<html lang="en">
<head>
<meta charset="utf-8">
<title>Trench Line Contracting Inc – Business Card</title>
<link href="https://fonts.googleapis.com/css2?family=Source+Sans+3:wght@400;600;700&display=swap" rel="stylesheet">
<style>
  :root {
    --orange: #f15a29;
    --charcoal: #1c1c1c;
    --grey: #6d6e70;
    --white: #ffffff;
    --backdrop: #ecebea;
  }
  * { margin: 0; padding: 0; box-sizing: border-box; }
  html, body {
    width: 1200px;
    height: 900px;
    overflow: hidden;
    background: var(--backdrop);
    font-family: "Source Sans 3", "Myriad Pro", sans-serif;
  }
  .canvas { position: relative; width: 1200px; height: 900px; }

  .card { position: absolute; overflow: hidden; box-shadow: 0 6px 18px rgba(0,0,0,0.18); }

  /* Contact side */
  .card-back { left: 238px; top: 62px; width: 555px; height: 343px; display: flex; }
  .contact-panel {
    width: 290px; height: 100%;
    background: var(--orange);
    color: var(--white);
    padding: 60px 0 0 32px;
  }
  .brand-panel { flex: 1; background: var(--charcoal); }

  .person-name { font-size: 19px; font-weight: 600; line-height: 19px; margin-bottom: 2px; }
  .person-title { font-size: 13px; font-weight: 400; line-height: 14px; margin-bottom: 4px; opacity: 0.92; }
  .contact-line { display: flex; align-items: center; font-size: 15px; line-height: 19px; }
  .contact-line svg { width: 11px; height: 11px; margin-right: 9px; fill: var(--white); }
  .address-block { margin-top: 37px; }
  .address-block + .address-block { margin-top: 15px; }
  .address-title { font-size: 17px; font-weight: 600; line-height: 20px; }
  .address-line { font-size: 15px; line-height: 20px; }

  /* Brand side */
  .card-front {
    left: 457px; top: 518px; width: 560px; height: 342px;
    background: var(--white);
    display: flex; flex-direction: column; align-items: center;
    padding-top: 92px;
  }
  .brand-dot { width: 64px; height: 64px; border-radius: 50%; background: var(--orange); margin-bottom: 44px; }
  .company-name {
    color: var(--grey);
    font-weight: 700;
    text-transform: uppercase;
    text-align: center;
    letter-spacing: 1px;
  }
  .company-name .line-main { display: block; font-size: 34px; line-height: 34px; }
  .company-name .line-sub { display: block; font-size: 17px; line-height: 22px; letter-spacing: 2px; }
</style>
</head>
<body>
<div class="canvas">

  <section class="card card-back">
    <div class="contact-panel">
      <p class="person-name">Daniel Harper</p>
      <p class="person-title">Project Manager</p>
      <p class="contact-line">
        <svg viewBox="0 0 24 24" aria-hidden="true"><path d="M6.6 10.8a15.1 15.1 0 0 0 6.6 6.6l2.2-2.2c.3-.3.7-.4 1-.2 1.1.4 2.3.6 3.6.6.6 0 1 .4 1 1V20c0 .6-.4 1-1 1C10.6 21 3 13.4 3 4c0-.6.4-1 1-1h3.5c.6 0 1 .4 1 1 0 1.3.2 2.5.6 3.6.1.3 0 .7-.2 1z"/></svg>
        044-555 010 234
      </p>
      <p class="contact-line">
        <svg viewBox="0 0 24 24" aria-hidden="true"><path d="M2 5h20v14H2z M2 5l10 8 10-8" /></svg>
        info@trenchline.example
      </p>
      <div class="address-block">
        <p class="address-title">Shop Address</p>
        <p class="address-line">12345, Address Goes Here</p>
        <p class="address-line">Country Name, 123456.</p>
      </div>
      <div class="address-block">
        <p class="address-title">Mailing Address</p>
        <p class="address-line">12345, Address Goes Here</p>
        <p class="address-line">Country Name, 123456.</p>
      </div>
    </div>
    <div class="brand-panel"></div>
  </section>

  <section class="card card-front">
    <div class="brand-dot"></div>
    <p class="company-name">
      <span class="line-main">Trench Line</span>
      <span class="line-sub">Contracting Inc</span>
    </p>
  </section>

</div>
</body>
</html>
```